Wordpress website for Dance Studio

Hi there, I am looking for Wordpress Website for dance studio. Happy for designed to use available themes. Would like a few pages setup and I can do the rest.

Other things I would like included in this theme :

Nice images page OR moving banner
Blog
Ability for youtubes

Other than that, simple requirements, just a gorgeous looking landing page/site etc.

Target Market(s)

Dance mums and kids (dancers)

Industry/Entity Type

Dance and Performancer

Coding

Coded - Design and coding required

Number of Pages Required

4 page

Font styles to use
Sans Serif

Colors
EB3D1F
EC4F4E
F09395
F8D3D4
FCEDEE

Requirements
Must have
• Wordpress theme
Nice to have
• Artistic, graphical, dance studio theme

```html
<!DOCTYPE html>
<html lang="en">
<head>
<meta charset="utf-8">
<title>Step &amp; Twirl Dance Studio</title>
<link href="https://fonts.googleapis.com/css2?family=Montserrat:wght@400;500;600;700&display=swap" rel="stylesheet">
<style>
:root{
  --red:#EB3D1F;
  --coral:#EC4F4E;
  --rose:#F09395;
  --blush:#F8D3D4;
  --pale:#FCEDEE;
  --ink:#222222;
  --text:#555555;
  --dark:#262626;
  --white:#ffffff;
}
*{margin:0;padding:0;box-sizing:border-box}
html,body{width:1200px;height:3660px;overflow:hidden}
body{font-family:'Montserrat',sans-serif;color:var(--ink);background:var(--white);position:relative}
.abs{position:absolute}
.btn{position:absolute;display:flex;align-items:center;justify-content:center;background:var(--red);color:var(--white);font-weight:700;font-size:15px;border-radius:30px;text-transform:uppercase}

/* header & hero */
.hero{position:absolute;left:0;top:0;width:1200px;height:720px;background:radial-gradient(ellipse at 50% 85%,#e6dcae 0%,#8a8a62 14%,#2f4a4c 40%,#1c2a2c 70%),#223233;overflow:hidden}
.hero-photo{position:absolute;inset:0;background:radial-gradient(ellipse at 50% 8%,rgba(214,150,60,.55),transparent 45%),linear-gradient(180deg,rgba(120,80,30,.35),transparent 40%)}
.brand{position:absolute;left:110px;top:28px;font-weight:700;font-size:22px;color:var(--white);letter-spacing:-.3px}
.nav{position:absolute;left:422px;top:31px;display:flex;gap:24px;font-weight:600;font-size:14.5px;color:var(--white)}
.social{position:absolute;display:flex;gap:7px}
.social span{width:36px;height:36px;border-radius:50%;background:var(--white);display:block;position:relative}
.social span::after{content:"";position:absolute;left:13px;top:13px;width:10px;height:10px;border-radius:50%;background:var(--red)}
.hero-box{position:absolute;left:243px;top:207px;width:713px;height:228px;background:rgba(40,40,40,.4);text-align:center;color:var(--white)}
.hero-box h1{margin-top:30px;font-size:35px;font-weight:700;text-transform:uppercase}
.hero-box p{margin-top:12px;font-size:20px;font-weight:700;text-transform:uppercase}
.arrow{position:absolute;top:290px;width:20px;height:34px}
.wave{position:absolute;left:0;top:0}

/* about */
.about-frame{position:absolute;left:111px;top:782px;width:488px;height:361px;border:2px solid #ececec;border-radius:14px;padding:6px;background:var(--white);box-shadow:0 2px 6px rgba(0,0,0,.08)}
.about-photo{width:100%;height:100%;border-radius:10px;background:linear-gradient(135deg,#e9e4dc 0%,#f3a66a 45%,#e8688a 70%,#cfc8c0 100%)}
.about-title{position:absolute;left:646px;top:790px;font-size:40px;font-weight:600}
.about-text{position:absolute;left:646px;top:860px;width:443px;font-size:14.5px;line-height:25.7px;color:var(--text);text-align:justify}

/* learn */
.learn{position:absolute;left:0;top:1237px;width:1200px;height:427px;background:linear-gradient(90deg,#4a3a3c,#3c2e36 40%,#3a3440 60%,#5a4a44);color:var(--white);text-align:center}
.learn h2{margin-top:55px;font-size:40px;font-weight:600}
.learn p{width:880px;margin:18px auto 0;font-size:14px;line-height:25.7px;font-weight:500}
.learn p + p{margin-top:17px}

/* videos */
.videos{position:absolute;left:0;top:1664px;width:1200px;height:575px;background:var(--pale)}
.sec-title{position:absolute;left:0;width:1200px;text-align:center;font-size:40px;font-weight:700;text-transform:uppercase}
.sec-title em{font-style:normal;color:var(--red)}
.video-main{position:absolute;left:300px;top:158px;width:599px;height:342px;background:var(--white);padding:6px;box-shadow:0 2px 6px rgba(0,0,0,.1)}
.video-fill{width:100%;height:100%;background:linear-gradient(180deg,#dcd9d0 0%,#bfb7aa 45%,#8c6a4e 80%,#6e4f39 100%);position:relative}
.play{position:absolute;left:50%;top:50%;width:46px;height:32px;margin:-16px 0 0 -23px;background:var(--red);border-radius:7px}
.play::after{content:"";position:absolute;left:18px;top:9px;border-left:12px solid var(--white);border-top:7px solid transparent;border-bottom:7px solid transparent}
.video-side{position:absolute;top:226px;height:207px;opacity:.85}

/* blog */
.card{position:absolute;background:var(--white);box-shadow:0 0 8px rgba(0,0,0,.1)}
.date{display:inline-block;background:var(--red);color:var(--white);font-size:12.5px;font-weight:600;padding:7px 13px;border-radius:16px}
.card h3{font-size:17px;font-weight:600;line-height:28px;text-transform:uppercase;color:var(--ink)}
.card p{font-size:14.5px;line-height:23px;color:#777}
.blog-photo{position:absolute}

/* newsletter */
.newsletter{position:absolute;left:0;top:2931px;width:1200px;height:460px;background:linear-gradient(90deg,rgba(236,79,78,.92),rgba(240,100,95,.88) 50%,rgba(236,79,78,.92)),#d8a080;color:var(--white);text-align:center}
.newsletter h2{margin-top:60px;font-size:28px;font-weight:700;text-transform:uppercase}
.newsletter p{margin-top:10px;font-size:15px}
.signup{position:absolute;left:216px;top:153px;width:767px;height:50px;background:var(--white);border-radius:25px;border:2px solid var(--white);text-align:left}
.signup span{position:absolute;left:17px;top:14px;font-size:15px;color:#555}
.signup b{position:absolute;right:3px;top:3px;width:144px;height:40px;border-radius:20px;background:var(--red);color:var(--white);font-size:15px;display:flex;align-items:center;justify-content:center}

/* footer */
.footer{position:absolute;left:0;top:3380px;width:1200px;height:280px;background:var(--dark);color:var(--white);text-align:center}
.footer .f-brand{margin-top:20px;font-size:28px;font-weight:700;letter-spacing:-.4px}
.f-links{margin-top:14px;display:flex;justify-content:center;gap:32px;font-size:20px}
.f-legal{margin-top:12px;display:flex;justify-content:center;gap:28px;font-size:18px}
.rule{position:absolute;left:111px;top:223px;width:978px;height:1px;background:#555}
.copy{position:absolute;left:0;top:241px;width:1200px;font-size:13px}
</style>
</head>
<body>

<header class="hero">
  <div class="hero-photo" role="img" aria-label="Young ballerina in a tutu dancing on a lit stage"></div>
  <div class="brand">STEP &amp; TWIRL</div>
  <nav class="nav"><span>Home</span><span>About Us</span><span>What We Do</span><span>Latest Blog</span><span>Contact Us</span></nav>
  <div class="social" style="left:969px;top:22px"><span></span><span></span><span></span></div>
  <div class="hero-box">
    <h1>Welcome to Step &amp; Twirl</h1>
    <p>Lorem ipsum dolor sit amet, consectetur</p>
  </div>
  <div class="btn" style="left:520px;top:342px;width:160px;height:53px">Get Started</div>
  <svg class="arrow" style="left:42px" viewBox="0 0 20 34"><path d="M17 3 L4 17 L17 31" fill="none" stroke="#fff" stroke-width="4"/></svg>
  <svg class="arrow" style="left:1138px" viewBox="0 0 20 34"><path d="M3 3 L16 17 L3 31" fill="none" stroke="#fff" stroke-width="4"/></svg>
  <svg class="wave" width="1200" height="720" viewBox="0 0 1200 720">
    <path d="M0 698 C120 585 290 528 420 532 C620 540 760 710 960 706 C1090 700 1160 610 1200 530 V720 H0Z" fill="#EB3D1F"/>
    <path d="M0 720 V712 C160 620 310 568 440 572 C630 580 760 725 1000 720 Z" fill="#ffffff"/>
  </svg>
</header>

<section class="about">
  <div class="about-frame"><div class="about-photo" role="img" aria-label="Dance teacher leading a class of women and girls"></div></div>
  <h2 class="about-title">ABOUT US</h2>
  <p class="about-text">Lorem ipsum dolor sit amet, consectetur adipiscing elit, sed do eiusmod tempor incididunt ut labore et dolore magna aliqua. Ut enim ad minim veniam, quis nostrud exercitation ullamco laboris nisi ut aliquip ex ea commodo consequat. Duis aute irure dolor in reprehenderit in voluptate velit esse cillum dolor enim ad minim veniam, quis nostrud exer citation ullamco laboris nisi ut aliquipea.</p>
  <div class="btn" style="left:646px;top:1075px;width:152px;height:52px">Learn More</div>
</section>

<section class="learn" role="img" aria-label="Children dancing together in a studio">
  <h2>LEARN TO DANCE</h2>
  <p>Lorem ipsum dolor sit amet, consectetur adipiscing elit, sed do eiusmod tempor incididunt ut labore et dolore magna aliqua. Ut enim ad minim veniam, quis nostrud exercitation ullamco laboris nisi ut aliquip ex ea commodo consequat. Duis aute irure dolor in reprehenderit in voluptate velit esse cillum dolorea.</p>
  <p>Quis nostrud exercitation ullamco laboris nisi ut aliquip ex ea commodo consequat. Duis aute irure dolor in repreh enderit in voluptate velit esse cillum dolorea.</p>
  <div class="btn" style="left:524px;top:311px;width:152px;height:52px">Book Now</div>
</section>

<section class="videos">
  <h2 class="sec-title" style="top:70px">Featured <em>Videos</em></h2>
  <div class="video-side" style="left:0;width:182px;background:linear-gradient(180deg,#b8bcc0,#8d9196)" role="img" aria-label="Dance studio with children rehearsing"></div>
  <div class="video-main"><div class="video-fill" role="img" aria-label="Children dancing in a mirrored studio"><div class="play"></div></div></div>
  <div class="video-side" style="left:1017px;width:183px;background:linear-gradient(180deg,#f4f2ef,#e7d9c6)" role="img" aria-label="Girls dancing in a bright studio"></div>
</section>

<section class="blog">
  <h2 class="sec-title" style="top:2322px">Latest <em>Blog</em></h2>
  <article class="card" style="left:111px;top:2404px;width:480px;height:430px">
    <div class="blog-photo" style="left:7px;top:6px;width:466px;height:261px;background:linear-gradient(120deg,#7a4a3a,#c9b8a4 45%,#e0d8cc 70%,#9a8a7c)" role="img" aria-label="Girls in a ballet class raising their arms"></div>
    <div class="date abs" style="left:40px;top:248px">09 NOV 2021</div>
    <h3 class="abs" style="left:40px;top:300px;width:420px">Lorem ipsum dolor sit amet, consec tet adipiscing elitm dolo</h3>
    <p class="abs" style="left:40px;top:370px;width:430px">Sed ut perspiciatis unde omnis iste natus error sit volup tatem accusants iste natus erroque.</p>
  </article>
  <article class="card" style="left:609px;top:2404px;width:480px;height:202px">
    <div class="blog-photo" style="left:6px;top:6px;width:180px;height:190px;background:linear-gradient(135deg,#d8dde0,#b9c0c4 50%,#ccb6a0)" role="img" aria-label="Teacher stretching with a young dancer"></div>
    <div class="date abs" style="left:212px;top:22px">09 NOV 2021</div>
    <h3 class="abs" style="left:212px;top:74px;width:250px">Lorem ipsum dolor sit consec tetur adipi</h3>
    <p class="abs" style="left:212px;top:138px;width:250px">Sed ut perspiciatis unde omnis iste na tus error sit volua.</p>
  </article>
  <article class="card" style="left:609px;top:2633px;width:480px;height:202px">
    <div class="blog-photo" style="left:6px;top:6px;width:180px;height:190px;background:linear-gradient(135deg,#c8cf5a,#e0cf4a 40%,#e39a7a 75%,#8a6aa0)" role="img" aria-label="Happy children dancing with their teacher"></div>
    <div class="date abs" style="left:212px;top:22px">09 NOV 2021</div>
    <h3 class="abs" style="left:212px;top:74px;width:250px">Lorem ipsum dolor sit consec tetur adipi</h3>
    <p class="abs" style="left:212px;top:138px;width:250px">Sed ut perspiciatis unde omnis iste na tus error sit volua.</p>
  </article>
</section>

<section class="newsletter" role="img" aria-label="Kids dancing, tinted in coral">
  <h2>Sign up our newsletter</h2>
  <p>Join our mailing list to receive the latest news and updates from our team</p>
  <div class="signup"><span>Email Address</span><b>SIGN UP</b></div>
</section>

<svg class="abs" style="left:0;top:3190px" width="1200" height="192" viewBox="0 0 1200 192">
  <path d="M0 175 C180 60 380 40 600 100 C820 160 1020 175 1200 55 V192 H0Z" fill="#EB3D1F"/>
  <path d="M0 192 V185 C190 80 390 60 600 118 C820 178 1020 195 1200 78 V192 Z" fill="#262626"/>
</svg>

<footer class="footer">
  <div class="f-brand">STEP &amp; TWIRL</div>
  <div class="f-links"><span>Home</span><span>About Us</span><span>What We Do</span><span>Latest Blog</span><span>Contact Us</span></div>
  <div class="f-legal"><span>Privacy Policy</span><span>Terms &amp; Conditions</span></div>
  <div class="social" style="left:539px;top:154px"><span></span><span></span><span></span></div>
  <div class="rule"></div>
  <div class="copy">Copyrights 2021 <b>STEP &amp; TWIRL</b>. All Rights Reserved</div>
</footer>

</body>
</html>
```